We need a label design for our company, Ridgefern Hemp. We produce organic CBD oil and CBD infusing products. This label will be used on our new line of 1oz-3oz CBD oil. We would like the design to include our company logo and QR code, which I will add in the upload files area. The label should also have an area with our ingredients, which are:
CBD oil, Peppermint oil, Lavender oil, Eucalyptus oil, Cinnamon oil, Clove oil, and Vitamin E.
The final product should appeal to customer and be eye catching.

```html
<!DOCTYPE html>
<html lang="en">
<head>
<meta charset="utf-8">
<title>Ridgefern Hemp – CBD Oil Label</title>
<link href="https://fonts.googleapis.com/css2?family=Montserrat:wght@500;600;700&display=swap" rel="stylesheet">
<style>
  :root {
    --page-bg: #4a4a4a;
    --white: #ffffff;
    --green: #12b214;
    --green-dark: #1a9a22;
    --navy: #1d4a96;
    --blue: #1f5fc4;
    --blue-deep: #17449a;
    --panel-dark: #161616;
    --panel-mid: #262626;
    --lime: #c9e24b;
    --gold: #e9c54a;
  }
  * { margin: 0; padding: 0; box-sizing: border-box; }
  html, body {
    width: 1200px; height: 762px; overflow: hidden;
    background: var(--page-bg);
    font-family: "Montserrat", sans-serif;
  }
  .label {
    position: absolute; left: 337px; top: 31px;
    width: 526px; height: 700px;
    background: var(--white);
    box-shadow: 0 10px 30px rgba(0,0,0,.45);
    overflow: hidden;
  }
  .top-band { position: absolute; left: 0; top: 0; width: 100%; height: 13px; background: var(--green); }
  .brand-mark {
    position: absolute; left: 213px; top: 38px;
    width: 100px; height: 100px; border-radius: 50%;
    background: var(--navy);
  }
  .brand-name {
    position: absolute; left: 0; top: 150px; width: 100%;
    text-align: center; color: var(--navy);
    font-weight: 600; font-size: 31px; letter-spacing: 2px;
    text-transform: uppercase;
  }
  .green-band {
    position: absolute; left: 0; top: 225px; width: 100%; height: 150px;
    background: linear-gradient(90deg, var(--green-dark), var(--green) 45%, var(--green-dark));
  }
  .drip-edge { position: absolute; left: 0; top: 0; width: 526px; height: 700px; }
  .product-name {
    position: absolute; left: 0; top: 274px; width: 100%;
    text-align: center; color: var(--white);
    font-weight: 700; font-size: 74px; letter-spacing: 3px; line-height: 1;
  }
  .blue-rule { position: absolute; left: 0; top: 374px; width: 100%; height: 3px; background: var(--blue-deep); }
  .dark-panel {
    position: absolute; left: 0; top: 377px; width: 100%; height: 303px;
    background: linear-gradient(90deg, var(--panel-dark), var(--panel-mid));
  }
  .natural-pill {
    position: absolute; left: 95px; top: 353px; width: 338px; height: 47px;
    border-radius: 24px;
    background: linear-gradient(90deg, var(--blue), var(--blue-deep));
    color: var(--white); font-weight: 600; font-size: 29px; letter-spacing: 1px;
    display: flex; align-items: center; justify-content: center;
  }
  .ingredients { position: absolute; left: 54px; top: 448px; list-style: none; }
  .ingredients li {
    display: flex; align-items: center; gap: 7px;
    height: 27px; color: var(--lime);
    font-weight: 600; font-size: 16.5px; letter-spacing: .3px;
  }
  .ingredients svg { width: 14px; height: 14px; flex: none; }
  .hero-art {
    position: absolute; left: 210px; top: 410px; width: 268px; height: 248px;
    background: radial-gradient(ellipse at 62% 55%, rgba(255,220,110,.85), rgba(200,160,50,.45) 40%, rgba(30,30,30,0) 72%);
  }
  .gold-rule { position: absolute; left: 0; top: 680px; width: 100%; height: 3px; background: var(--gold); }
  .bottom-band { position: absolute; left: 0; top: 683px; width: 100%; height: 17px; background: var(--green); }
  .size-tab {
    position: absolute; left: 162px; top: 661px; width: 203px; height: 39px;
    border-radius: 18px 18px 0 0; background: var(--green);
    color: var(--white); font-weight: 600; font-size: 17px; letter-spacing: 1px;
    display: flex; align-items: center; justify-content: center;
  }
</style>
</head>
<body>
<main class="label">
  <div class="top-band"></div>
  <div class="brand-mark"></div>
  <div class="brand-name">Ridgefern Hemp</div>

  <div class="green-band"></div>
  <svg class="drip-edge" viewBox="0 0 526 700" aria-hidden="true">
    <path fill="#ffffff" d="M0 225 V240 Q10 246 17 241 V262 A3.5 3.5 0 0 0 24 262 V241 Q40 234 55 242 Q66 247 78 240 Q88 236 92 242 V256 A3 3 0 0 0 98 256 V242 Q115 236 130 244 Q145 250 160 241 Q165 238 167 243 V268 A3.5 3.5 0 0 0 174 268 V243 Q190 236 205 244 Q215 249 227 242 V254 A3 3 0 0 0 233 254 V242 Q250 235 268 243 Q282 249 296 241 V262 A3.5 3.5 0 0 0 303 262 V241 Q320 236 335 244 Q345 248 352 243 V258 A3 3 0 0 0 358 258 V243 Q380 235 400 244 Q415 249 428 242 V266 A3.5 3.5 0 0 0 435 266 V242 Q450 236 465 244 Q478 249 488 241 V256 A3 3 0 0 0 494 256 V241 Q510 235 526 240 V225 Z"/>
  </svg>
  <h1 class="product-name">CBD OIL</h1>

  <div class="blue-rule"></div>
  <section class="dark-panel"></section>
  <div class="natural-pill">100% NATURAL</div>

  <ul class="ingredients">
    <li><svg viewBox="0 0 14 14"><circle cx="7" cy="7" r="6" fill="none" stroke="#c9e24b" stroke-width="1.4"/><path d="M4.2 7.2 L6.2 9.1 L9.9 5.2" fill="none" stroke="#c9e24b" stroke-width="1.4"/></svg>CBD oil</li>
    <li><svg viewBox="0 0 14 14"><circle cx="7" cy="7" r="6" fill="none" stroke="#c9e24b" stroke-width="1.4"/><path d="M4.2 7.2 L6.2 9.1 L9.9 5.2" fill="none" stroke="#c9e24b" stroke-width="1.4"/></svg>Peppermint oil</li>
    <li><svg viewBox="0 0 14 14"><circle cx="7" cy="7" r="6" fill="none" stroke="#c9e24b" stroke-width="1.4"/><path d="M4.2 7.2 L6.2 9.1 L9.9 5.2" fill="none" stroke="#c9e24b" stroke-width="1.4"/></svg>Lavender oil</li>
    <li><svg viewBox="0 0 14 14"><circle cx="7" cy="7" r="6" fill="none" stroke="#c9e24b" stroke-width="1.4"/><path d="M4.2 7.2 L6.2 9.1 L9.9 5.2" fill="none" stroke="#c9e24b" stroke-width="1.4"/></svg>Eucalyptus oil</li>
    <li><svg viewBox="0 0 14 14"><circle cx="7" cy="7" r="6" fill="none" stroke="#c9e24b" stroke-width="1.4"/><path d="M4.2 7.2 L6.2 9.1 L9.9 5.2" fill="none" stroke="#c9e24b" stroke-width="1.4"/></svg>Cinnamon oil</li>
    <li><svg viewBox="0 0 14 14"><circle cx="7" cy="7" r="6" fill="none" stroke="#c9e24b" stroke-width="1.4"/><path d="M4.2 7.2 L6.2 9.1 L9.9 5.2" fill="none" stroke="#c9e24b" stroke-width="1.4"/></svg>Clove oil</li>
    <li><svg viewBox="0 0 14 14"><circle cx="7" cy="7" r="6" fill="none" stroke="#c9e24b" stroke-width="1.4"/><path d="M4.2 7.2 L6.2 9.1 L9.9 5.2" fill="none" stroke="#c9e24b" stroke-width="1.4"/></svg>Vitamin E</li>
  </ul>

  <div class="hero-art" role="img" aria-label="Glowing golden hemp leaf with an oil droplet"></div>

  <div class="gold-rule"></div>
  <div class="bottom-band"></div>
  <div class="size-tab">1 OZ (30ML)</div>
</main>
</body>
</html>
```